Orthodox Christian Youth Conference Flyer/Agenda

We are seeking a designer to help us take our award winning conference to the next level with a pamphlet that will outline the agenda of the 3 day conference but will also include pictures, illustrations, and visuals so that we build some excitement and interest. We also need to be able to make adjustments and corrections to the pamphlet's text, leading up to the conference and would like it in a file that could permit us to edit it without having to bother you!

Target Market(s)

To be used to promote conference and agenda

Industry/Entity Type

Christian

Font styles to use
Serif
Sans Serif

Requirements
Must have
• include logo, photos and visuals

```html
<!DOCTYPE html>
<html lang="en">
<head>
<meta charset="utf-8">
<title>Holy Vine Youth Conference Pamphlet</title>
<link rel="stylesheet" href="https://fonts.googleapis.com/css2?family=Oswald:wght@500;700&family=Open+Sans:wght@400;600;700&family=Merriweather:wght@400;700&display=swap">
<style>
:root{
  --olive:#8fa33a;
  --olive-dark:#6f8226;
  --charcoal:#2c2c2a;
  --ink:#333;
  --paper:#ffffff;
  --stage:#e9e6e1;
  --photo-warm:#b9a07a;
  --photo-sky:#9fb6c9;
  --photo-green:#7d9253;
}
*{margin:0;padding:0;box-sizing:border-box}
html,body{width:889px;height:1200px;overflow:hidden;background:var(--stage);font-family:"Open Sans",Arial,sans-serif;color:var(--ink)}
.spread{position:relative;width:889px;height:1200px}
.page{position:absolute;width:412px;height:560px;background:var(--paper);overflow:hidden;box-shadow:0 2px 8px rgba(0,0,0,.25)}
.p1{left:22px;top:30px}.p2{left:455px;top:30px}.p3{left:22px;top:615px}.p4{left:455px;top:615px}
.abs{position:absolute}
.photo{position:absolute;border:2px solid #fff;box-shadow:0 1px 3px rgba(0,0,0,.3)}
.sky{background:linear-gradient(180deg,var(--photo-sky),#d8d2c0)}
.warm{background:linear-gradient(160deg,var(--photo-warm),#6d5a44)}
.green{background:linear-gradient(180deg,#a8b98a,var(--photo-green))}
.hall{background:linear-gradient(180deg,#8b6b4f,#3e3128)}
.banner{position:absolute;font-family:"Oswald",sans-serif;font-weight:700;text-transform:uppercase;color:#fff;line-height:1}
.small{font-size:5.2px;line-height:1.45}
.tiny{font-size:4.6px;line-height:1.45}
.h-sub{font-family:"Merriweather",serif;font-weight:700;font-size:6px;color:var(--olive-dark);margin-top:4px}
.wave{position:absolute;left:0;bottom:0;width:412px}
.kicker{font-size:5px;color:#666}
.title{font-family:"Oswald",sans-serif;font-weight:700;color:var(--charcoal);font-size:11px;line-height:1.05;text-transform:uppercase}
.q{font-weight:700;color:var(--olive-dark);font-size:5.4px;margin-top:5px}
.contact{font-family:"Oswald",sans-serif;font-weight:500;color:var(--charcoal);font-size:10px;line-height:1.25}
</style>
</head>
<body>
<main class="spread">

<section class="page p1">
  <div class="abs" style="left:14px;top:14px;width:200px">
    <p class="kicker">Holy Vine Orthodox Church · Riverbend Parish Council</p>
    <h1 class="title" style="margin-top:6px">The 2015 Holy Vine Orthodox Youth<br>and Family Conference at Riverbend</h1>
    <p class="tiny" style="margin-top:4px">Three days of worship, learning and fellowship for youth and families.</p>
  </div>
  <svg class="abs" style="left:222px;top:14px" width="190" height="46"><path d="M14 0H190V46H0Z" fill="var(--charcoal)"/><path d="M22 4H190V42H8Z" fill="var(--olive)"/></svg>
  <div class="banner" style="left:250px;top:21px;font-size:12px;text-align:center;width:150px">Description<br>of Event</div>
  <div class="abs small" style="left:232px;top:68px;width:166px">Join us for our annual conference where young people and their families gather to pray, learn about the faith and build lasting friendships. Each day begins with prayer and closes with shared meals, talks and games. All ages are welcome to attend.</div>
  <svg class="abs" style="left:0;top:72px" width="222" height="44"><path d="M0 0H212L222 44H0Z" fill="var(--charcoal)"/><path d="M0 4H206L214 40H0Z" fill="var(--olive)"/></svg>
  <div class="banner" style="left:14px;top:78px;font-size:15px">Program Agenda</div>
  <div class="abs" style="left:14px;top:96px;font-family:Oswald,sans-serif;font-size:7px;color:#fff">for Youth and Family Conference 2015</div>
  <div class="abs small" style="left:14px;top:124px;width:205px">
    <p class="h-sub">Thursday, October 8th, 2015 "Arrival and Welcome"</p>
    <p>3:00 pm Registration opens in the parish hall<br>5:00 pm Vespers followed by welcome dinner<br>7:30 pm Opening talk and icebreaker games<br>9:30 pm Evening prayers and rest</p>
    <p class="h-sub">Friday, October 9th, 2015 "Growing in Faith and Friendship"</p>
    <p>8:00 am Morning prayers and breakfast<br>9:30 am Workshops for youth and parents<br>12:30 pm Lunch and free time outdoors<br>3:00 pm Service project in the community<br>7:00 pm Talent night and fellowship</p>
    <p class="h-sub">Saturday, October 10th, 2015 "Serving One Another"</p>
    <p>9:00 am Divine service and group talks<br>1:00 pm Lunch, sports and hikes<br>6:00 pm Vigil followed by dinner</p>
    <p class="h-sub">Sunday, October 11th, 2015 "Going Forth in Peace"</p>
    <p>9:00 am Liturgy, closing meal and farewells</p>
  </div>
  <div class="photo sky" style="left:236px;top:124px;width:160px;height:150px" role="img" aria-label="Photo of a church bell tower with a golden onion dome"></div>
  <div class="photo warm" style="left:236px;top:284px;width:160px;height:140px" role="img" aria-label="Illustration of a saint icon"></div>
  <svg class="wave" height="80" viewBox="0 0 412 80" preserveAspectRatio="none"><path d="M0 40Q200 0 412 30V80H0Z" fill="var(--charcoal)"/><path d="M0 50Q200 12 412 42V80H0Z" fill="var(--olive)"/></svg>
</section>

<section class="page p2">
  <div class="photo sky" style="left:14px;top:14px;width:170px;height:110px" role="img" aria-label="Photo of the conference center building"></div>
  <div class="abs" style="left:196px;top:14px;font-family:Oswald,sans-serif;font-size:11px;color:var(--charcoal)">Opportunity to <span style="color:var(--olive);font-size:15px;font-weight:700">DONATE</span></div>
  <div class="abs small" style="left:196px;top:38px;width:96px">Your gift helps families attend, covers meals and keeps the retreat open for every young person who wishes to come.</div>
  <div class="photo green" style="left:298px;top:36px;width:100px;height:70px" role="img" aria-label="Photo of a lake with trees"></div>
  <div class="abs small" style="left:14px;top:132px;width:170px">The retreat grounds offer open fields, a quiet chapel and a large hall for meals and talks. Donations of any size are gratefully received.</div>
  <div class="photo hall" style="left:196px;top:114px;width:100px;height:74px" role="img" aria-label="Photo of a hall with a stage"></div>
  <div class="abs small" style="left:300px;top:118px;width:98px">Checks may be made out to the parish youth fund and mailed to the church office.</div>
  <svg class="abs" style="left:0;top:200px" width="412" height="40"><path d="M0 0H160Q190 20 220 0H412V40H0Z" fill="var(--charcoal)"/><path d="M0 34H412V40H0Z" fill="var(--olive)"/></svg>
  <div class="banner" style="left:150px;top:206px;font-size:12px;text-align:center;width:112px">Program<br>Information</div>
  <div class="abs small" style="left:14px;top:250px;width:185px">
    <p class="h-sub">For Youth and Families</p>
    <p>Sessions are arranged by age so that children, teens and parents each hear talks suited to them. Families share meals and services together every day of the gathering.</p>
    <p class="h-sub">Speakers and Guests</p>
    <p>Clergy and lay teachers from parishes across the region lead workshops on prayer, scripture, service and family life.</p>
    <p class="h-sub">What to Bring</p>
    <p>Sleeping bag, modest clothing, outdoor shoes, a notebook and a joyful spirit.</p>
  </div>
  <div class="abs small" style="left:212px;top:250px;width:186px">
    <p class="h-sub">Registration</p>
    <p>Register online or at your parish office before September 20th. Early registration includes a conference shirt and guaranteed lodging.</p>
    <p class="h-sub">Fees</p>
    <p>Youth $60 · Adults $80 · Family rate $200<br>Day passes $25 per person</p>
    <p class="h-sub">Lodging</p>
    <p>Cabins are assigned by age and family. Nearby hotel rooms may be booked directly by guests.</p>
  </div>
  <svg class="wave" height="70" viewBox="0 0 412 70" preserveAspectRatio="none"><path d="M0 30Q210 0 412 24V70H0Z" fill="var(--charcoal)"/><path d="M0 40Q210 10 412 34V70H0Z" fill="var(--olive)"/></svg>
</section>

<section class="page p3">
  <svg class="abs" style="left:0;top:14px" width="190" height="44"><path d="M0 0H176L190 44H0Z" fill="var(--charcoal)"/><path d="M0 4H170L180 40H0Z" fill="var(--olive)"/></svg>
  <div class="banner" style="left:14px;top:20px;font-size:24px">FAQs</div>
  <div class="photo warm" style="left:198px;top:10px;width:200px;height:80px" role="img" aria-label="Photo of clergy and youth gathered in church"></div>
  <div class="abs small" style="left:14px;top:96px;width:384px">
    <p class="q">Who may attend the conference?</p>
    <p>All Orthodox youth and their families are welcome, as are friends who wish to learn more about the faith.</p>
    <p class="q">Is there an age limit for youth sessions?</p>
    <p>Youth sessions are for ages 12 to 19. Younger children join the family program with their parents.</p>
    <p class="q">Can I attend only one day?</p>
    <p>Yes. Day passes include meals and all sessions for that day. Please register in advance so we can plan.</p>
    <p class="q">Will there be chaperones?</p>
    <p>Trained adult volunteers stay with each youth group at all times, including in the cabins at night.</p>
    <p class="q">What about special diets?</p>
    <p>Tell us on your form and the kitchen team will gladly prepare meals to suit your needs and the fasting rule.</p>
    <p class="q">Is financial help available?</p>
    <p>Scholarships are offered through parish gifts. Speak with your priest or contact the committee chair.</p>
    <p class="q">How do I get there?</p>
    <p>Directions and shared ride lists are sent by email two weeks before the event begins.</p>
  </div>
  <div class="photo hall" style="left:14px;top:300px;width:110px;height:150px" role="img" aria-label="Photo of a priest speaking to a group"></div>
  <div class="abs small" style="left:136px;top:306px;width:262px">
    <p class="q">What should I wear?</p>
    <p>Modest dress for services and comfortable clothes for sports, hikes and outdoor activities.</p>
    <p class="q">Can parents volunteer?</p>
    <p>Yes, we always need help with meals, games and set up. Mark the volunteer box on your form.</p>
  </div>
  <svg class="wave" height="50" viewBox="0 0 412 50" preserveAspectRatio="none"><path d="M130 20Q280 0 412 14V50H130Z" fill="var(--charcoal)"/><path d="M130 28Q280 8 412 22V50H130Z" fill="var(--olive)"/></svg>
</section>

<section class="page p4">
  <div class="photo warm" style="left:14px;top:14px;width:384px;height:150px" role="img" aria-label="Group photo of conference participants in front of the church"></div>
  <svg class="abs" style="left:0;top:150px" width="412" height="60" viewBox="0 0 412 60" preserveAspectRatio="none"><path d="M0 30Q200 0 412 20V34Q200 16 0 44Z" fill="var(--olive)"/></svg>
  <div class="photo sky" style="left:14px;top:190px;width:120px;height:180px" role="img" aria-label="Photo of the church tower and onion dome"></div>
  <div class="abs small" style="left:148px;top:200px;width:250px">
    <p style="font-weight:700;font-size:6px">Holy Vine Orthodox Church</p>
    <p>120 Chapel Road, Riverbend</p>
    <p>Phone: 555-014-2290</p>
    <p>youthconf@holyvine.org</p>
  </div>
  <svg class="wave" height="200" viewBox="0 0 412 200" preserveAspectRatio="none"><path d="M0 60Q200 0 412 40V200H0Z" fill="var(--charcoal)"/><path d="M0 72Q200 12 412 52V200H0Z" fill="var(--olive)"/></svg>
  <div class="abs contact" style="left:140px;top:470px;width:260px;text-align:right;color:#fff">Contact Youth Conference Committee Chair, Andrei Volkov<br>youthconf@holyvine.org · 555-014-2290</div>
</section>

</main>
</body>
</html>
```